Brand New Product Needs Sales Focused Website Design

Looking for design of Homepage, Category Page & Product Page for single product sales focused website. TrundleCrate manufacture and distribute a brand new product to the market called PalTote-Case which is a super strong, re-useable, folding & stacking plastic box which can be seen on our current website www.paltote-case.example PalTote-Case was originally developed as an alternative to supermarket carrier bags and was pitched as a box for life against the other low end re-useable products. The original version was made from recycled plastic and pitched very much as environmental product. We are now taking a different direction and have re-designed the boxes in 5 bright and fashionable designs and although we still want the primary focus to be supermarket shopping we want to position the product as a design led, must have shopping and household accessory rather than a boring, cheap looking black plastic box. The new designs will still have the environmental benefits of being able to be re-used thousands of times and being 100% recyclable and save on the imminent 5p tax on carrier bags in the UK however the new designs will not be made from recycled material. Although the main use for PalTote-Case is supermarket shopping it has a multitude of other uses especially where you need temporary storage - laundry, back of the car, moving house/students, gardening, days out, home office filing (will take A4 file), recycling and much more - PalTote-Case is made out of super strong Polypropylene and can be easily washed and sanitised after use and can be folded and unfolded thousands of times and so will last for many years. PalTote-Case is a product that needs to be seen in action to be understood so the web design must quickly and easily communicate what PalTote-Case is and how it works - this can be done with video, images and copy. Our current website does not work for many reasons:- it is too busy, has too much information, tries too hard and ultimately isn't working. Any of the images off our current website can be supplied for use. Once the concept of the website is agreed I can get these photoshopped with the new designs. Pictures of new designs for reference will be attached to this brief. Ultimately we want the website to convert visitors to sales and therefore designers with a proven track record in this field are especially welcome to enter. We also have a Dropbox folder with over 100 product and situation images in - please send email address and we will send an invite to the folder. Due to Christmas period this competition will be run over 15 days however we may choose to extend the deadline to account for the non working days. Any questions feel free to ask - we will respond within 24 hours where possible.

```html
<!DOCTYPE html>
<html lang="en">
<head>
<meta charset="utf-8">
<title>PalTote-Case — Home</title>
<link href="https://fonts.googleapis.com/css2?family=Open+Sans:wght@400;600;700&family=Raleway:wght@400;500&family=Lato:wght@400;700&display=swap" rel="stylesheet">
<style>
:root{
  --orange:#f7941d;
  --orange-deep:#f26f21;
  --red:#e0231b;
  --ink:#4a4a4a;
  --muted:#777;
  --line:#e3e3e3;
  --page:#f4f2ee;
  --panel:#ffffff;
  --footer:#2f3036;
  --footer-text:#8b8c92;
  --link-blue:#2a7bbf;
}
*{box-sizing:border-box;margin:0;padding:0}
html,body{width:877px;height:1200px;overflow:hidden}
body{background:var(--page);font-family:"Open Sans",sans-serif;color:var(--ink);position:relative;border-top:3px solid var(--orange)}
.abs{position:absolute}
a{color:inherit;text-decoration:none}

/* top bar */
.search{left:80px;top:7px;width:124px;height:21px;border:1px solid #d5d5d5;background:#fff;font-size:9px;color:#999;padding:4px 6px}
.utility{left:214px;top:11px;font-size:9.5px;color:#666;display:flex;gap:12px}
.cart{left:700px;top:13px;font-size:9px;color:#555;font-weight:600;display:flex;gap:5px;align-items:center}
.corner{left:781px;top:0;width:16px;height:20px;background:var(--orange);clip-path:polygon(0 0,100% 0,100% 100%)}
.corner::after{content:"+";position:absolute;right:2px;top:-2px;color:#fff;font-size:9px;font-weight:700}

/* header */
.header{left:80px;top:33px;width:717px;height:66px;background:#fff;border-bottom:1px solid #d6d6d6}
.brand{left:16px;top:20px;display:flex;align-items:center;gap:7px;font-family:"Open Sans",sans-serif;font-weight:700;font-size:19px;color:var(--orange)}
.brand-mark{width:14px;height:14px;border-radius:50%;background:var(--orange)}
.nav{right:15px;top:27px;display:flex;gap:32px;font-family:"Raleway",sans-serif;font-size:12.5px;color:#555}

/* hero */
.hero{left:80px;top:98px;width:717px;height:268px;background:#fff}
.hero-title{left:26px;top:46px;font-size:42px;font-weight:700;color:var(--orange);letter-spacing:-.5px;line-height:1}
.hero-sub{left:26px;top:108px;font-family:"Raleway",sans-serif;font-size:20px;color:#555;border-top:1px solid #999;border-bottom:1px solid #999;padding:0 0 1px;line-height:1.2}
.hero-copy{left:27px;top:142px;width:250px;font-size:9px;line-height:10.5px;color:#444}
.btn{font-family:"Open Sans",sans-serif;font-weight:600;font-size:12px;display:flex;align-items:center;justify-content:center;border-radius:2px}
.btn-solid{left:26px;top:195px;width:90px;height:29px;background:var(--orange-deep);color:#fff}
.btn-ghost{left:139px;top:194px;width:89px;height:31px;border:1px solid var(--orange);color:var(--orange);background:#fff}
.hero-photo{left:408px;top:0;width:256px;height:268px;background:linear-gradient(180deg,#2fb56b 0%,#2fb56b 14%,#f2f2f0 22%,#f7f4f2 60%,#b8d04a 88%,#2d3447 100%)}

/* features */
.feature{top:375px;width:235px;height:115px;background:#fff;text-align:center}
.feature h3{font-family:"Raleway",sans-serif;font-weight:500;font-size:18.5px;color:var(--orange);margin-top:26px;display:flex;justify-content:center;align-items:center;gap:8px}
.feature p{font-family:"Raleway",sans-serif;font-size:12px;color:#666;margin-top:13px}

/* tabs and products */
.tab{top:506px;height:33px;font-family:"Raleway",sans-serif;font-size:12.5px;display:flex;align-items:center;justify-content:center}
.tab-active{left:81px;width:120px;background:var(--orange-deep);color:#fff;font-family:"Open Sans",sans-serif;font-weight:600}
.tab-idle{left:201px;width:118px;background:#f7f7f7;border:1px solid #ddd;color:#555}
.products{left:81px;top:539px;width:534px;height:437px;background:#fff}
.product{width:163px}
.product-photo{width:161px;height:113px;border:1px solid #ddd;background:#fff;position:relative}
.product-photo .fill{position:absolute;left:14px;top:26px;width:108px;height:60px;background:linear-gradient(180deg,#f3f1ee 0%,#eeeae6 70%,#b7cf46 100%)}
.product-photo .tag{position:absolute;left:125px;top:26px;width:26px;height:26px;background:var(--orange-deep);border-radius:4px;transform:rotate(40deg)}
.product h4{font-family:"Lato",sans-serif;font-weight:700;font-size:10.3px;line-height:12px;color:#333;margin:10px 0 0 5px}
.product .was{font-size:9.2px;color:var(--link-blue);text-decoration:line-through;margin:3px 0 0 5px}
.product .row{display:flex;justify-content:space-between;align-items:center;margin:3px 3px 0 5px}
.product .now{font-weight:700;font-size:12px;color:var(--red)}
.product .add{background:var(--orange-deep);color:#fff;font-size:8px;font-weight:700;width:68px;height:17px;display:flex;align-items:center;justify-content:center}

/* sidebar */
.side{left:622px;width:173px;background:#fff}
.side h3{font-family:"Open Sans",sans-serif;font-weight:700;font-size:14.5px;color:var(--orange);padding:12px 7px 0}
.side-head{height:41px;border-bottom:4px solid var(--page)}
.cat-list{list-style:none;padding:6px 8px 0}
.cat-list li{font-size:8px;color:#444;height:19px;display:flex;justify-content:space-between;align-items:center;border-bottom:1px dotted #ccc}
.cat-list li span.plus{width:7px;height:7px;background:#ccc;position:relative}
.shopper{top:638px;height:178px;background:linear-gradient(180deg,#fff 0%,#f7f4ef 40%,#e7d774 60%,#2a2a2a 95%)}
.news-copy{font-size:8px;line-height:12px;color:#444;padding:8px 8px 0}
.news-input{margin:6px 0 0 8px;width:114px;height:20px;border:1px solid #ddd;font-size:8px;color:#555;padding:5px 4px}
.news-btn{margin:9px 0 0 9px;width:74px;height:25px;background:var(--orange-deep);color:#fff;font-size:11px;font-weight:600;display:flex;align-items:center;justify-content:center}

/* footer */
.footer{left:0;top:1003px;width:877px;height:197px;background:var(--footer);border-top:3px solid var(--orange)}
.footer-corner{left:776px;top:1004px;width:20px;height:20px;background:var(--orange);clip-path:polygon(0 0,100% 0,100% 100%)}
.footer-corner::after{content:"+";position:absolute;right:3px;top:-1px;color:#fff;font-size:9px;font-weight:700}
.fcol{top:1025px}
.fcol h5{font-family:"Open Sans",sans-serif;font-weight:600;font-size:11.5px;color:#fff;margin-bottom:5px}
.fcol li{list-style:none;font-size:9px;color:var(--footer-text);line-height:16px}
.fcol p{font-size:9px;color:var(--footer-text);line-height:16px;width:180px}
.f-form{left:616px;top:1080px;display:flex}
.f-form .field{width:126px;height:23px;background:#fff;font-size:7.5px;font-style:italic;color:#777;padding:7px 8px}
.f-form .go{width:57px;height:23px;background:var(--orange-deep);color:#fff;font-size:10px;font-weight:600;display:flex;align-items:center;justify-content:center}
.follow{left:616px;top:1113px;font-size:11px;color:#fff;font-weight:600}
.socials{left:618px;top:1135px;display:flex;gap:7px}
.socials span{width:16px;height:16px;border-radius:50%;background:#fff}
.f-rule{left:0;top:1166px;width:877px;height:1px;background:#3b3c42}
.copyright{left:0;top:1177px;width:877px;text-align:center;font-size:9px;color:#777}
</style>
</head>
<body>

<div class="abs search">Search</div>
<div class="abs utility"><a>Account</a><a>Checkout</a><a>Log In</a><a>Register</a></div>
<div class="abs cart">
  <svg width="16" height="12" viewBox="0 0 16 12" aria-hidden="true"><path d="M1 1h3l2 7h8l1-5H5" fill="none" stroke="#f7941d" stroke-width="1.6"/><circle cx="7" cy="10.5" r="1.2" fill="#f7941d"/><circle cx="13" cy="10.5" r="1.2" fill="#f7941d"/></svg>
  CART EMPTY
</div>
<div class="abs corner"></div>

<header class="abs header">
  <div class="abs brand"><span class="brand-mark"></span>PalTote-Case</div>
  <nav class="abs nav"><a>Home</a><a>Why Bags</a><a>How to Use</a><a>About Us</a><a>Contact Us</a></nav>
</header>

<section class="abs hero">
  <h1 class="abs hero-title">PalTote-Case</h1>
  <div class="abs hero-sub">Recommended for Best Bags</div>
  <p class="abs hero-copy">Lorem ipsum dolor sit amet, consectetur adipiscing elit, sed do eiusmod tempor incididunt ut labore et dolore magna aliqua.</p>
  <a class="abs btn btn-solid">Learn More</a>
  <a class="abs btn btn-ghost">View All</a>
  <div class="abs hero-photo" role="img" aria-label="Person carrying a floral patterned folding box by its handles"></div>
</section>

<div class="abs feature" style="left:81px">
  <h3><svg width="16" height="16" viewBox="0 0 16 16" aria-hidden="true"><path d="M6 2L1 7l5 5M1 7h8a5 5 0 0 1 5 5v2" fill="none" stroke="#f7941d" stroke-width="2"/></svg>Guarantee</h3>
  <p>Lorem Ipsum dolor sit amet</p>
</div>
<div class="abs feature" style="left:322px">
  <h3 style="margin-top:25px"><svg width="25" height="16" viewBox="0 0 25 16" aria-hidden="true"><rect x="9" y="1" width="15" height="10" fill="#f7941d"/><path d="M1 11V6l3-4h5v9z" fill="#f7941d"/><circle cx="5" cy="13" r="2.3" fill="#f7941d"/><circle cx="19" cy="13" r="2.3" fill="#f7941d"/></svg>Free Shipping</h3>
  <p style="margin-top:12px">Lorem Ipsum dolor sit amet</p>
</div>
<div class="abs feature" style="left:562px">
  <h3><svg width="20" height="20" viewBox="0 0 20 20" aria-hidden="true"><rect x="4" y="4" width="12" height="12" transform="rotate(-40 10 10)" fill="none" stroke="#f7941d" stroke-width="2"/><path d="M7 10l3-3M9 12l3-3" stroke="#f7941d" stroke-width="1.5"/></svg>Newsletter</h3>
  <p>Lorem Ipsum dolor sit amet</p>
</div>

<div class="abs tab tab-active">Feature Products</div>
<div class="abs tab tab-idle">Latest Products</div>
<section class="abs products"></section>

<article class="abs product" style="left:94px;top:562px"><div class="product-photo" role="img" aria-label="Floral folding box with buy tag"><span class="fill"></span><span class="tag"></span></div><h4>Lorem Ipsum Dolor Sit Amet Consectutuer</h4><p class="was">Don't Pay $12.32</p><div class="row"><span class="now">Today $3.99</span><a class="add">Add to Cart</a></div></article>
<article class="abs product" style="left:269px;top:562px"><div class="product-photo" role="img" aria-label="Floral folding box with buy tag"><span class="fill"></span><span class="tag"></span></div><h4>Lorem Ipsum Dolor Sit Amet Consectutuer</h4><p class="was">Don't Pay $30.02</p><div class="row"><span class="now">Today $9.98</span><a class="add">Add to Cart</a></div></article>
<article class="abs product" style="left:440px;top:562px"><div class="product-photo" role="img" aria-label="Floral folding box with buy tag"><span class="fill"></span><span class="tag"></span></div><h4>Lorem Ipsum Dolor Sit Amet Consectutuer</h4><p class="was">Don't Pay $12.32</p><div class="row"><span class="now">Today $2.29</span><a class="add">Add to Cart</a></div></article>
<article class="abs product" style="left:94px;top:776px"><div class="product-photo" role="img" aria-label="Floral folding box with buy tag"><span class="fill"></span><span class="tag"></span></div><h4>Lorem Ipsum Dolor Sit Amet Consectutuer</h4><p class="was">Don't Pay $12.32</p><div class="row"><span class="now">Today $3.99</span><a class="add">Add to Cart</a></div></article>
<article class="abs product" style="left:269px;top:776px"><div class="product-photo" role="img" aria-label="Floral folding box with buy tag"><span class="fill"></span><span class="tag"></span></div><h4>Lorem Ipsum Dolor Sit Amet Consectutuer</h4><p class="was">Don't Pay $30.02</p><div class="row"><span class="now">Today $9.98</span><a class="add">Add to Cart</a></div></article>
<article class="abs product" style="left:440px;top:776px"><div class="product-photo" role="img" aria-label="Floral folding box with buy tag"><span class="fill"></span><span class="tag"></span></div><h4>Lorem Ipsum Dolor Sit Amet Consectutuer</h4><p class="was">Don't Pay $12.32</p><div class="row"><span class="now">Today $2.29</span><a class="add">Add to Cart</a></div></article>

<aside class="abs side" style="top:497px;height:131px">
  <div class="side-head"><h3>CATEGORY</h3></div>
  <ul class="cat-list">
    <li>Lorem Ipsum<span class="plus"></span></li>
    <li>Lorem Ipsum<span class="plus"></span></li>
    <li>Lorem Ipsum<span class="plus"></span></li>
    <li>Lorem Ipsum<span class="plus"></span></li>
  </ul>
</aside>
<div class="abs side shopper" role="img" aria-label="Smiling shopper holding many shopping bags"></div>
<aside class="abs side" style="top:822px;height:136px">
  <div class="side-head"><h3>NEWSLETTER</h3></div>
  <p class="news-copy">Ready to get our newsletter?<br>Enter your email</p>
  <div class="news-input">E-mail</div>
  <a class="news-btn">Subscribe</a>
</aside>

<footer class="abs footer"></footer>
<div class="abs footer-corner"></div>
<div class="abs fcol" style="left:82px"><h5>Site Links</h5><ul><li>Home</li><li>About Us</li><li>Shop Our Products</li><li>Need Help</li></ul></div>
<div class="abs fcol" style="left:213px"><h5>About PalTote Case</h5><ul><li>Our Mission</li><li>Blog</li><li>Why Choose Us</li></ul></div>
<div class="abs fcol" style="left:349px"><h5>Our Boxes</h5><ul><li>Watch A Live Demo</li><li>View Our Products</li><li>Smartphone Apps</li></ul></div>
<div class="abs fcol" style="left:482px"><h5>Having Trouble?</h5><ul><li>Knowledge Base</li><li>Discussion Forum</li><li>Contact Us</li></ul></div>
<div class="abs fcol" style="left:616px"><h5>Our Newsletter</h5><p>Subscribe To Our E-mail List for Sales &amp; Updates.</p></div>
<div class="abs f-form"><span class="field">Email..</span><a class="go">Subscribe</a></div>
<div class="abs follow">Follow Us On :</div>
<div class="abs socials"><span></span><span></span><span></span><span></span></div>
<div class="abs f-rule"></div>
<div class="abs copyright">Copyrights 2014 PalTote Case - All Rights Reserved</div>

</body>
</html>
```